Tellmora Corporate Stationery

Look for design of all new corporate stationery for an existing insurance broking business that is going through a redesign and move from older partners to younger family members. New Logo is attached. Company is Brisbane based.
Colours in the Logo is Hex #43bed8 and website features a lot of hex #17b8d8. Website front page "A plan to protect you" - headline. "Professional and Individual advice to protect your greatest assets" - tagline.

Stationery required: Business Cards, Letter head, Thank-you cards, Birthday cards, Presentation folders, With Compliment slips and a powerpoint template. We also would like to send a card to all customers with the something along of the lines of "something new".

Target Market(s)

Customers of Insurance business looking at superannuation, life and income protection insurance, investment advice and wills

Industry/Entity Type

Insurance Broker

Font styles to use
Other font styles liked:
• same as logo

Requirements
Must have
• The above designs for new stationery for the new business including:
• Business Cards, Letter head, Thank-you cards, Birthday cards, Presentation folders, With Compliment slips and a powerpoint template. We also would like to send a card to all customers with the something along of the lines of "something new".
Nice to have
• It is a new look - long time family business being passed to next generation - big focus on advice for YOU, individual advice etc..

```html
<!DOCTYPE html>
<html lang="en">
<head>
<meta charset="utf-8">
<title>Tellmora Business Card</title>
<link rel="stylesheet" href="https://fonts.googleapis.com/css2?family=Open+Sans:ital,wght@0,400;0,600;1,400&display=swap">
<style>
  :root {
    --teal: #3dbfd9;
    --teal-soft: #e9f6f9;
    --grey-mark: #7d7d7d;
    --ink: #555555;
    --paper: #ffffff;
    --backdrop: #2a2a2a;
  }
  * { margin: 0; padding: 0; box-sizing: border-box; }
  html, body {
    width: 1200px; height: 987px; overflow: hidden;
    background: var(--backdrop);
    font-family: "Open Sans", Arial, sans-serif;
  }
  .card {
    position: absolute; left: 293px; width: 615px; height: 352px;
    overflow: hidden;
  }
  .card--front { top: 130px; background: var(--paper); }
  .card--back { top: 505px; background: var(--teal); }

  .brand-band {
    position: absolute; left: 0; top: 56px; width: 41px; height: 72px;
    background: var(--teal);
  }
  .brand-dot {
    position: absolute; left: 28px; top: 56px; width: 72px; height: 72px;
    border-radius: 50%; background: var(--paper);
    border: 10px solid var(--grey-mark);
  }
  .brand-name {
    position: absolute; left: 127px; top: 68px;
    font-size: 31px; font-weight: 600; letter-spacing: 1px;
    color: var(--teal); line-height: 1;
  }
  .deco-ring {
    position: absolute; right: -150px; top: -40px;
    width: 430px; height: 430px; border-radius: 50%;
    border: 22px solid #f2f2f2;
  }

  .person-name {
    position: absolute; left: 127px; top: 150px;
    font-size: 22px; font-weight: 600; color: var(--teal); line-height: 1;
  }
  .person-role {
    position: absolute; left: 127px; top: 180px;
    font-size: 16px; color: var(--ink); line-height: 1;
  }
  .contact-list { position: absolute; left: 127px; top: 226px; list-style: none; }
  .contact-list li {
    display: flex; align-items: center; height: 23.5px;
    font-size: 15.5px; color: var(--ink);
  }
  .contact-list svg { width: 16px; height: 16px; margin-right: 7px; fill: var(--teal); }
  .divider {
    position: absolute; left: 340px; top: 250px; width: 1.5px; height: 66px;
    background: var(--ink);
  }
  .address { position: absolute; left: 359px; top: 248px; font-size: 15.5px; color: var(--ink); line-height: 23px; }

  .back-mark {
    position: absolute; right: 36px; top: 226px;
    display: flex; align-items: center; gap: 10px;
  }
  .back-dot { width: 26px; height: 26px; border-radius: 50%; background: var(--grey-mark); }
  .back-name { font-size: 28px; font-weight: 600; color: var(--paper); letter-spacing: 1px; line-height: 1; }
  .back-web {
    position: absolute; right: 31px; top: 314px;
    font-size: 15px; font-style: italic; color: var(--paper);
  }
</style>
</head>
<body>
  <section class="card card--front">
    <div class="deco-ring"></div>
    <div class="brand-band"></div>
    <div class="brand-dot"></div>
    <div class="brand-name">TELLMORA</div>

    <div class="person-name">DANIEL HART</div>
    <div class="person-role">CEO/FOUNDER</div>

    <ul class="contact-list">
      <li><svg viewBox="0 0 16 16"><path d="M3.5 1.5l2.5 0 1 3.5-1.8 1.3c.8 1.8 2.2 3.2 4 4l1.3-1.8 3.5 1v2.5c0 .8-.7 1.5-1.5 1.5C6.8 13.5 2 8.7 2 3c0-.8.7-1.5 1.5-1.5z"/></svg>612 555 0148</li>
      <li><svg viewBox="0 0 16 16"><path d="M4.5 0.5h7a1 1 0 0 1 1 1v13a1 1 0 0 1-1 1h-7a1 1 0 0 1-1-1v-13a1 1 0 0 1 1-1zm.5 2v9.5h6V2.5zm3 10.3a.9.9 0 1 0 0 1.8.9.9 0 0 0 0-1.8z"/></svg>612 555 0193</li>
      <li><svg viewBox="0 0 16 16"><path d="M4 1h8v4H4zM1.5 6h13a1 1 0 0 1 1 1v5h-3v3h-9v-3h-3V7a1 1 0 0 1 1-1zm3 6v2h7v-2z"/></svg>612 555 0127</li>
      <li><svg viewBox="0 0 16 16"><path d="M1 3.5h14v9H1zm1.3 1.2L8 9l5.7-4.3z" /></svg>hello@tellmora.au</li>
    </ul>

    <div class="divider"></div>
    <div class="address">
      24 Wattle Grove<br>
      Brisbane, QLD 4000<br>
      www.tellmora.au
    </div>
  </section>

  <section class="card card--back">
    <div class="back-mark">
      <div class="back-dot"></div>
      <div class="back-name">TELLMORA</div>
    </div>
    <div class="back-web">www.tellmora.au</div>
  </section>
</body>
</html>
```